Modern Business Card

Modern professional business card with more than just logo and demographic info. Something memorable.

We are a trendy/modern chiropractic group with an emphasis on neurology, hence the minimalist-type brain logo. We want to convey that modern and technical aspect with professionalism and the elite nature of our practice environment.

```html
<!DOCTYPE html>
<html lang="en">
<head>
<meta charset="utf-8">
<title>Cadence Chiropractic — Business Card</title>
<link href="https://fonts.googleapis.com/css2?family=Crimson+Text:wght@400;700&family=Arimo:wght@400&display=swap" rel="stylesheet">
<style>
  :root {
    --backdrop: #8c8c8c;
    --card: #1f1e1d;
    --pattern: rgba(255,255,255,0.07);
    --brand: #d2d2d2;
    --brand-mark: #7a7a7a;
    --name: #a3a3a3;
    --text: #c4c4c4;
    --text-soft: #b0b0b0;
    --rule: #3a3938;
    --sheen: rgba(255,255,255,0.04);
  }
  * { margin: 0; padding: 0; box-sizing: border-box; }
  html, body { width: 1200px; height: 900px; overflow: hidden; }
  body {
    background: var(--backdrop);
    position: relative;
    font-family: "Arimo", Arial, sans-serif;
  }
  .card {
    position: absolute;
    left: 333px;
    width: 554px;
    height: 343px;
    border-radius: 14px;
    background: var(--card);
    overflow: hidden;
    box-shadow: 0 3px 8px rgba(0,0,0,0.35);
  }
  .card--front { top: 92px; }
  .card--back { top: 471px; }
  .card__glow {
    position: absolute;
    inset: 0;
    background: radial-gradient(ellipse 60% 70% at 25% 10%, var(--sheen), transparent 70%);
  }
  .card__pattern {
    position: absolute;
    top: 0;
    border-radius: 0 0 40px 40px;
    background: linear-gradient(180deg, var(--pattern) 0%, rgba(255,255,255,0.04) 55%, transparent 100%);
  }
  .card--front .card__pattern { left: 10px; width: 340px; height: 270px; }
  .card--back .card__pattern { left: 25px; width: 335px; height: 275px; }

  .brand {
    position: absolute;
    display: flex;
    align-items: center;
    gap: 14px;
    font-family: "Crimson Text", Georgia, serif;
    font-weight: 400;
    color: var(--brand);
  }
  .brand__dot {
    width: 62px;
    height: 62px;
    border-radius: 50%;
    background: var(--brand-mark);
    flex: none;
  }
  .brand__name { line-height: 0.95; letter-spacing: 0.5px; }
  .brand__name span { display: block; }
  .brand__line1 { font-size: 48px; }
  .brand__line2 { font-size: 25px; }
  .card--front .brand { left: 188px; top: 62px; }
  .card--back .brand { left: 112px; top: 132px; }

  .person {
    position: absolute;
    left: 32px;
    top: 196px;
    right: 32px;
  }
  .person__name {
    display: flex;
    align-items: center;
    gap: 8px;
    font-family: "Crimson Text", Georgia, serif;
    font-weight: 700;
    font-size: 16px;
    letter-spacing: 0.6px;
    color: var(--name);
  }
  .person__name::after {
    content: "";
    flex: 1;
    height: 1px;
    background: var(--rule);
  }
  .person__role { font-size: 14.5px; color: var(--text); margin-top: 2px; }

  .contact {
    position: absolute;
    left: 30px;
    top: 250px;
    list-style: none;
    font-size: 15px;
    color: var(--text);
  }
  .contact li { display: flex; align-items: center; gap: 8px; height: 20.5px; }
  .contact svg { width: 17px; height: 17px; flex: none; }

  .address {
    position: absolute;
    right: 34px;
    top: 270px;
    text-align: right;
    font-size: 15px;
    line-height: 20.5px;
    color: var(--text-soft);
    font-style: normal;
  }
</style>
</head>
<body>

<section class="card card--front" aria-label="Business card front">
  <div class="card__glow"></div>
  <div class="card__pattern" role="img" aria-label="Faint decorative pattern of tall rounded vertical bars"></div>
  <div class="brand">
    <span class="brand__dot"></span>
    <div class="brand__name"><span class="brand__line1">CADENCE</span><span class="brand__line2">CHIROPRACTIC</span></div>
  </div>

  <div class="person">
    <p class="person__name">MARCUS HALE</p>
    <p class="person__role">Managing Director</p>
  </div>

  <ul class="contact">
    <li>
      <svg viewBox="0 0 18 18" aria-hidden="true"><rect x="1" y="1" width="16" height="16" rx="2" fill="none" stroke="#c4c4c4" stroke-width="1.4"/><path d="M6 4.5l2 2-1.2 1.4c.6 1.4 1.7 2.5 3.2 3.2L11.4 10l2 2-1.3 1.6C8.3 13.3 4.7 9.7 4.4 5.9z" fill="#c4c4c4"/></svg>
      044-555 201 347
    </li>
    <li>
      <svg viewBox="0 0 18 18" aria-hidden="true"><rect x="1" y="4" width="16" height="11" fill="#c4c4c4"/><path d="M1 4l8 6 8-6" fill="none" stroke="#1f1e1d" stroke-width="1.4"/></svg>
      hello@cadencespine.com
    </li>
    <li>
      <svg viewBox="0 0 18 18" aria-hidden="true"><g fill="none" stroke="#c4c4c4" stroke-width="1.3"><circle cx="9" cy="9" r="7.5"/><ellipse cx="9" cy="9" rx="3.2" ry="7.5"/><path d="M1.5 9h15M3 5h12M3 13h12"/></g></svg>
      www.cadencespine.com
    </li>
  </ul>

  <address class="address">88, Meridian Lane<br>Northvale, 45821</address>
</section>

<section class="card card--back" aria-label="Business card back">
  <div class="card__glow"></div>
  <div class="card__pattern" role="img" aria-label="Faint decorative pattern of tall rounded vertical bars"></div>
  <div class="brand">
    <span class="brand__dot"></span>
    <div class="brand__name"><span class="brand__line1">CADENCE</span><span class="brand__line2">CHIROPRACTIC</span></div>
  </div>
</section>

</body>
</html>
```